Residential Remodeling Contractor needs updated business card

I need a new design for my business card.
Name of the company is Ridgefell Construction. I need a card that commands presence, strength, integrity. I have been in business for 28 years. I am a Residential Remodeling Contractor that covers all aspects of a residential remodel and build.

```html
<!DOCTYPE html>
<html lang="en">
<head>
<meta charset="utf-8">
<title>Ridgefell Construction – Business Card</title>
<link rel="stylesheet" href="https://fonts.googleapis.com/css2?family=Libre+Caslon+Text:wght@700&family=Arimo:wght@400&display=swap">
<style>
  :root {
    --backdrop: #9a9a9a;
    --paper: #ffffff;
    --navy: #1b3a7c;
    --ink: #3a3a3a;
    --white: #ffffff;
  }
  * { margin: 0; padding: 0; box-sizing: border-box; }
  html, body { width: 1200px; height: 1059px; overflow: hidden; }
  body { background: var(--backdrop); position: relative; font-family: "Arimo", Arial, sans-serif; }

  .card { position: absolute; border-radius: 18px; overflow: hidden; }

  /* Front */
  .card-front { left: 256px; top: 89px; width: 688px; height: 390px; background: var(--paper); }
  .card-front .base-band { position: absolute; left: 0; right: 0; bottom: 0; height: 10px; background: var(--navy); }

  .wordmark { position: absolute; display: flex; align-items: center; gap: 14px; font-family: "Libre Caslon Text", Georgia, serif; font-weight: 700; line-height: 1.1; white-space: nowrap; }
  .wordmark .mark-square { flex: none; }
  .front-wordmark { left: 214px; top: 90px; color: var(--navy); font-size: 31px; }
  .front-wordmark .mark-square { background: var(--navy); width: 28px; height: 28px; }

  .person { position: absolute; left: 0; right: 0; top: 209px; text-align: center; }
  .person-name { font-family: "Libre Caslon Text", Georgia, serif; font-weight: 700; font-size: 24px; letter-spacing: 0.5px; color: var(--navy); line-height: 1.2; }
  .person-title { font-size: 16px; color: var(--ink); margin-top: 2px; }

  .address { position: absolute; right: 363px; top: 296px; text-align: right; font-size: 16px; line-height: 21px; color: var(--ink); white-space: nowrap; }
  .divider { position: absolute; left: 344px; top: 291px; width: 1px; height: 55px; background: var(--navy); }
  .contact-list { position: absolute; left: 366px; top: 283px; list-style: none; font-size: 16px; line-height: 22.5px; color: var(--ink); }
  .contact-list li { display: flex; align-items: center; gap: 8px; white-space: nowrap; }
  .contact-list svg { width: 13px; height: 13px; fill: var(--navy); flex: none; }
  .web-domain { color: var(--navy); }

  /* Back */
  .card-back { left: 253px; top: 569px; width: 694px; height: 394px; }
  .back-pattern { position: absolute; inset: 0; background: linear-gradient(110deg, #1d3570 0%, #213c7c 45%, #3f5f9f 80%, #6f8fc8 100%); }
  .back-wordmark { left: 452px; top: 282px; color: var(--white); font-size: 20px; gap: 12px; }
  .back-wordmark .mark-square { background: var(--white); width: 22px; height: 22px; }
</style>
</head>
<body>
  <section class="card card-front" aria-label="Business card front">
    <div class="wordmark front-wordmark">
      <span class="mark-square"></span>
      <span class="wordmark-text">Ridgefell<br>Construction</span>
    </div>

    <div class="person">
      <div class="person-name">DANIEL OKAFOR</div>
      <div class="person-title">Owner &amp; Manager</div>
    </div>

    <div class="address">P.O. Box&nbsp; Street Name<br>Country Name AB, A5B 521</div>
    <div class="divider"></div>
    <ul class="contact-list">
      <li>
        <svg viewBox="0 0 16 16" aria-hidden="true"><path d="M2 5c0-2 3-3 6-3s6 1 6 3v1h-3V5H5v1H2zM4 7h8l2 7H2z"/></svg>
        <span>555 214 0387</span>
      </li>
      <li>
        <svg viewBox="0 0 16 16" aria-hidden="true"><path d="M1 6l7-5 7 5v9H1zM2.5 6.5L8 10.5l5.5-4L8 2.8z"/></svg>
        <span>info@ridgefellconstruction.com</span>
      </li>
      <li>
        <svg viewBox="0 0 16 16" aria-hidden="true"><circle cx="8" cy="8" r="7"/><path d="M4 5c2 0 2 2 4 2s1 3-1 3-1 3-3 3" stroke="#fff" stroke-width="1.3" fill="none"/></svg>
        <span>www.<span class="web-domain">ridgefellconstruction</span>.com</span>
      </li>
    </ul>
    <div class="base-band"></div>
  </section>

  <section class="card card-back" aria-label="Business card back">
    <div class="back-pattern" role="img" aria-label="Repeating pattern of the company emblem fading from dark to light navy"></div>
    <div class="wordmark back-wordmark">
      <span class="mark-square"></span>
      <span class="wordmark-text">Ridgefell<br>Construction</span>
    </div>
  </section>
</body>
</html>
```